Bluefern Business Services needs a new interactive and interesting website

We need an interesting, professional, modern and functional company website for Bluefern Business Services - a young IT Services company based out of Chennai, India.

Bluefern Business Services is a fully owned subsidiary of Marlow Goods, one of the world's leading direct to consumer wine merchant.

We already have a registered company logo which must feature in the website.

We conceive, design, develop, test, implement and support IT solutions across the entire Marlow Goods IT landscape. For ex : We currently run about 25 e-commerce websites for Marlow Goods on ATG and Dot Net.

We would like to see our corporate colors used in the website. (Burgundy wine and wine green - source: www.bluefernbs-site.com)

We are looking at this website to communicate a fun, friendly and professionally managed company - reaching out to career seekers, prospective customers and general public.

For reference - The company name 'Bluefern' is an inspiration from the Marlow Goods lineage.

The second image with the world map is stickered on our main entrance to the office, I am not sure where this can be used -just putting it out there..

Please note that there are only a few more days to submit designs for this contest  !

I would appreciate if you can help posting your designs in time for our review and consideration.

Thanks.

Reason: Thanks for your inputs. We have a number of designers and a lot to digest and work with in the past few days. There has been a rush of new designs in the last few days Hence we will require more time to process these and make our decision. Hence i am requesting the contest to be open for more days. Regards, Tarun

Target Market(s)

Prospective job seekers who want to know more about the company and also wish to apply for a job vacancy
People wanting to know more about the company in general and our progress
People who want to see what we offer and how we can help them too - prospective customers
Companies that are interested in our IT Captive journey and are looking for a business opportunity

Industry/Entity Type

E-Commerce

Requirements
Must have
• Log In/ Register facility acting as a Single Sign on for Intranet (Employees)

Facility to post job vacancies (with an expiry date) and enable people to apply for a role and upload their CV/Resume.

Facility to Review Job applications

Facility for website visitors to contact Bluefern business Services via an online 'Contact Us' form with a split of job seekers and business opportunities

Gallery facility to upload pictures regarding company events
Nice to have
• Less Cluttered and contemporary design
Some Wine/Vineyard inspirations will be good but not too much, the company is an IT services company

```html
<!DOCTYPE html>
<html lang="en">
<head>
<meta charset="utf-8">
<title>Bluefern Business Services</title>
<link href="https://fonts.googleapis.com/css2?family=PT+Sans:wght@400;700&family=PT+Sans+Narrow:wght@700&display=swap" rel="stylesheet">
<style>
:root{
  --burgundy:#8c0f45;
  --burgundy-dark:#6e0a35;
  --burgundy-bright:#b0124f;
  --wine-green:#8cc43c;
  --ink:#222;
  --body:#333;
  --muted:#555;
  --sidebar:#f1f1f1;
  --band:#f4f4f4;
  --footer:#252525;
  --line:#c98aa6;
}
*{margin:0;padding:0;box-sizing:border-box}
html,body{width:900px;height:1200px;overflow:hidden;background:#fff}
body{position:relative;font-family:"PT Sans",Arial,sans-serif;color:var(--body)}
.abs{position:absolute}

.site-header{left:0;top:0;width:900px;height:114px;background:linear-gradient(180deg,#8f1049,#7d0c3e)}
.brand{left:86px;top:10px;display:flex;align-items:center;gap:12px;color:#fff;font-weight:700}
.brand-mark{width:42px;height:42px;border-radius:50%;background:#fff;opacity:.9}
.brand-name{font-size:54px;line-height:52px;letter-spacing:-1px}
.brand-sub{font-size:31px;line-height:34px;margin-top:2px}
.phone{left:637px;top:27px;width:169px;height:39px;border-radius:4px;background:var(--burgundy-dark);border:1px solid #a0305e;color:#fff;font-size:15px;display:flex;align-items:center;gap:8px;padding-left:10px}

.main-nav{left:0;top:114px;width:900px;height:35px;background:linear-gradient(#fff,#ececec);border-bottom:1px solid #ccc}
.main-nav a{position:absolute;top:0;height:35px;line-height:34px;font-size:12px;color:var(--burgundy);text-decoration:none;text-align:center}
.main-nav a.active{background:var(--burgundy);color:#fff;border-radius:10px;top:2px;height:31px;line-height:31px}
.nav-sep{position:absolute;top:0;width:1px;height:35px;background:#d6d6d6}

.hero{left:0;top:149px;width:900px;height:323px;background:linear-gradient(135deg,#a50f48,#cc1a5a 45%,#9c0f44 75%,#7e0c3a)}
.hero svg{position:absolute;left:0;top:0}
.hero-title{left:590px;top:61px;width:237px;height:26px;background:linear-gradient(#fff,#e8e8e8);border-radius:2px;font-size:15px;color:#222;text-align:right;padding-right:7px;line-height:27px;font-family:"PT Sans Narrow","PT Sans",sans-serif}
.hero-title span{color:var(--burgundy-bright)}
.hero-text{left:596px;top:100px;width:226px;font-size:10.5px;line-height:15.8px;color:#fff;text-align:right}
.btn-learn{left:718px;top:219px;width:101px;height:28px;background:var(--wine-green);color:#fff;font-family:"PT Sans Narrow","PT Sans",sans-serif;font-size:13px;line-height:28px;text-align:center;border-radius:2px}
.dots{left:764px;top:273px;display:flex;gap:5px;align-items:center}
.dots i{display:block;width:8px;height:8px;border-radius:50%;background:#e04a8a}
.dots i.on{width:11px;height:11px;background:transparent;border:2px solid #fff}

h2.section{position:absolute;font-size:17px;font-weight:400;color:var(--ink)}
h2.section span{color:var(--burgundy-bright)}
.rule{position:absolute;height:0;border-top:1px dotted var(--line)}
.lead{left:85px;top:529px;font-size:12px;color:var(--muted)}
.about-text{left:85px;top:550px;width:502px;font-size:9.6px;line-height:13.6px;color:#222;letter-spacing:-.15px}
.about-text p+p{margin-top:13.6px}
.btn-more{position:absolute;width:59px;height:27px;background:var(--burgundy);color:#fff;font-family:"PT Sans Narrow","PT Sans",sans-serif;font-size:12px;line-height:27px;text-align:center;border-radius:4px}

.service{position:absolute;top:751px;width:110px;text-align:center}
.service .icon{width:84px;height:84px;margin:0 auto;border-radius:50%;border:2px solid var(--burgundy);padding:6px;background:#fff}
.service .icon i{display:block;width:100%;height:100%;border-radius:50%}
.service .label{margin-top:12px;font-size:11.5px;line-height:15px;color:#444}

.sidebar{left:604px;top:480px;width:214px;height:480px;background:var(--sidebar)}
.sidebar-rule{left:612px;top:522px;width:192px}
.next-arrow{left:786px;top:498px;width:14px;height:14px;border-radius:50%;background:#555}
.event{position:absolute;left:614px;width:193px}
.event .photo{width:193px;height:82px}
.event h3{font-size:11.5px;font-weight:400;color:#222;margin-top:6px}
.event time{display:block;font-size:8px;color:#444;margin-top:3px}
.event p{font-size:8.4px;line-height:13.5px;color:#444;margin-top:5px;width:186px}
.event a{display:block;font-size:8.5px;color:var(--burgundy);margin-top:4px;text-decoration:none}

.clients-band{left:0;top:960px;width:900px;height:110px;background:var(--band)}
.client{position:absolute;top:978px;width:105px;height:71px;background:#fff;border:1px solid #d8d8d8;display:flex;align-items:center;justify-content:center;text-align:center;font-size:12px;font-weight:700;color:var(--burgundy);padding:4px}

.site-footer{left:0;top:1070px;width:900px;height:130px;background:linear-gradient(#2b2b2b,#1c1c1c)}
.social{left:86px;top:29px;display:flex;gap:9px}
.social i{display:block;width:20px;height:20px;border-radius:2px}
.footer-links{right:91px;top:30px;font-size:9.5px;color:#fff;text-align:right;line-height:18px}
</style>
</head>
<body>

<header class="site-header abs">
  <div class="brand abs">
    <div class="brand-mark"></div>
    <div>
      <div class="brand-name">Bluefern</div>
      <div class="brand-sub">Business Services</div>
    </div>
  </div>
  <div class="phone abs">
    <svg width="18" height="16" viewBox="0 0 18 16"><path d="M2 5c0-3 14-3 14 0v2h-4V5H6v2H2z" fill="#222"/><path d="M4 8h10l2 7H2z" fill="#222"/><circle cx="9" cy="11" r="2" fill="#6e0a35"/></svg>
    +91 (44) 55550123
  </div>
</header>

<nav class="main-nav abs">
  <a class="active" style="left:91px;width:84px">Home</a>
  <a style="left:188px;width:76px">About Us</a>
  <span class="nav-sep" style="left:267px"></span>
  <a style="left:270px;width:74px">Clients</a>
  <span class="nav-sep" style="left:344px"></span>
  <a style="left:346px;width:80px">Services</a>
  <span class="nav-sep" style="left:428px"></span>
  <a style="left:430px;width:72px">Careers</a>
  <span class="nav-sep" style="left:504px"></span>
  <a style="left:506px;width:150px">Current Opportunities</a>
  <span class="nav-sep" style="left:659px"></span>
  <a style="left:661px;width:110px">Contact Us</a>
</nav>

<section class="hero abs">
  <svg width="900" height="323" viewBox="0 0 900 323">
    <defs>
      <linearGradient id="heroPhoto" x1="0" y1="0" x2="1" y2="0">
        <stop offset="0" stop-color="#d9dfe6"/>
        <stop offset=".22" stop-color="#b9c9dc"/>
        <stop offset=".42" stop-color="#eef0f2"/>
        <stop offset=".62" stop-color="#e4d6cc"/>
        <stop offset=".82" stop-color="#f4f2ef"/>
        <stop offset="1" stop-color="#d8cfc6"/>
      </linearGradient>
      <linearGradient id="heroShade" x1="0" y1="0" x2="0" y2="1">
        <stop offset="0" stop-color="#ffffff" stop-opacity=".35"/>
        <stop offset=".6" stop-color="#ffffff" stop-opacity="0"/>
        <stop offset="1" stop-color="#8a8f98" stop-opacity=".35"/>
      </linearGradient>
      <radialGradient id="heroBottle" cx=".85" cy=".3" r=".35">
        <stop offset="0" stop-color="#5c0a2a" stop-opacity=".55"/>
        <stop offset="1" stop-color="#5c0a2a" stop-opacity="0"/>
      </radialGradient>
    </defs>
    <rect x="560" y="0" width="340" height="323" fill="url(#heroBottle)"/>
    <g role="img" aria-label="Photo of four colleagues smiling around a meeting table with a laptop">
      <path d="M0 0H568C598 60 590 140 574 200C560 250 548 300 558 323H0Z" fill="url(#heroPhoto)"/>
      <path d="M0 0H568C598 60 590 140 574 200C560 250 548 300 558 323H0Z" fill="url(#heroShade)"/>
    </g>
  </svg>
  <div class="hero-title abs">WELCOME TO <span>BLUEFERNBS</span></div>
  <p class="hero-text abs">Bluefern Business Services, an emerging provider of global IT consulting and software services. We are part of the Marlow Goods group, a family run business and the world's largest multi-channel home delivery wine merchant operating in the UK, USA, Australia, Germany, Hong Kong, Poland and Switzerland.</p>
  <div class="btn-learn abs">LEARN MORE</div>
  <div class="dots abs"><i class="on"></i><i></i><i></i><i></i></div>
</section>

<aside class="sidebar abs"></aside>

<main>
  <h2 class="section" style="left:83px;top:497px">Welcome to <span>Bluefern Business Services</span></h2>
  <div class="rule" style="left:86px;top:522px;width:497px"></div>
  <div class="lead abs">Delivering IT Excellence</div>
  <div class="about-text abs">
    <p>Welcome to Bluefern Business Services, an emerging provider of global IT consulting and software services. We are part of the Marlow Goods group, a family run business and the world's largest multi-channel home delivery wine merchant operating in the UK, USA, Australia, Germany, Hong Kong, Poland and Switzerland.</p>
    <p>Mainly based in the rich cultural city of Chennai in the south east of India, Bluefern Business Services' vision is to deliver outstanding technology solutions to all of the Marlow Goods' group companies that improve business processes, drive efficiencies, support rapid growth and elevate the overall customer experience to a different level.</p>
  </div>
  <div class="btn-more" style="left:524px;top:647px">More</div>

  <h2 class="section" style="left:83px;top:700px">Our <span>Services</span></h2>
  <div class="rule" style="left:86px;top:725px;width:497px"></div>
  <div class="service" style="left:78px"><div class="icon"><i role="img" aria-label="Illustration of a packaged software box with gears" style="background:radial-gradient(circle at 45% 35%,#6fa8dc,#dfe6ee 55%,#c9d1da 80%,#e7b0b0)"></i></div><div class="label">Packaged<br>Applications</div></div>
  <div class="service" style="left:206px"><div class="icon"><i role="img" aria-label="Illustration of connected servers" style="background:radial-gradient(circle at 50% 40%,#a9b3bd,#bfe8f2 45%,#e3e8ec 70%,#9aa4ad)"></i></div><div class="label">Enterprise<br>Application<br>Integration</div></div>
  <div class="service" style="left:334px"><div class="icon"><i role="img" aria-label="Illustration of a shopping cart with a mouse" style="background:radial-gradient(circle at 55% 45%,#2a2a2a,#c9ced3 40%,#eef0f2 65%,#e05a4a)"></i></div><div class="label">Digital<br>Commerce</div></div>
  <div class="service" style="left:461px"><div class="icon"><i role="img" aria-label="Illustration of a puzzle piece being placed" style="background:radial-gradient(circle at 55% 50%,#1f6fc0,#5fa3e0 35%,#e4e8ec 65%,#cfd5da)"></i></div><div class="label">Application<br>Development &amp;<br>Maintenance</div></div>
  <div class="btn-more" style="left:524px;top:903px">More</div>

  <h2 class="section" style="left:612px;top:497px">Company <span>Events</span></h2>
  <div class="rule sidebar-rule"></div>
  <div class="next-arrow abs"><svg width="14" height="14" viewBox="0 0 14 14"><path d="M6 4l3 3-3 3" stroke="#fff" stroke-width="1.5" fill="none"/></svg></div>

  <article class="event" style="top:530px">
    <div class="photo" role="img" aria-label="Video thumbnail of a vineyard with wine glasses and grapes" style="background:linear-gradient(100deg,#b98a2e,#d7b04a 35%,#7c7a3a 60%,#efe8d2 80%,#d9b84e)"></div>
    <h3>Etiam auctor ornare nibh</h3>
    <time>Jan 07, 2013</time>
    <p>Curabitur congue lorem massa, quis ultrices nibh rhoncus vel. Nunc quis sapien et nisl ultrices suscipit sit amet tristique lorem. sapien et nisl ultrices &nbsp;suscipit sit amet tristique lorem.</p>
    <a>More &gt;&gt;</a>
  </article>
  <article class="event" style="top:748px">
    <div class="photo" role="img" aria-label="Photo of a business team at an office event" style="background:linear-gradient(90deg,#e3ddd6,#6a5a52 22%,#2f3642 50%,#d8d2cc 72%,#3a3f4a 90%,#cfc9c4)"></div>
    <h3>Etiam auctor ornare nibh</h3>
    <time>Jan 07, 2013</time>
    <p>Curabitur congue lorem massa, quis ultrices nibh rhoncus vel. Nunc quis sapien et nisl ultrices suscipit sit amet tristique lorem. sapien et nisl ultrices &nbsp;suscipit sit amet tristique lorem.</p>
    <a>More &gt;&gt;</a>
  </article>

  <h2 class="section" style="left:86px;top:932px;color:var(--burgundy-bright)">Clients</h2>
</main>

<section class="clients-band abs"></section>
<div class="client" style="left:84px">Ledger Cellars</div>
<div class="client" style="left:210px">Brightvine</div>
<div class="client" style="left:334px">Halvers Wine Co</div>
<div class="client" style="left:456px">Maison Corde</div>
<div class="client" style="left:580px">Weekend Wine Circle</div>
<div class="client" style="left:703px">Southern Cellar</div>

<footer class="site-footer abs">
  <div class="social abs">
    <i style="background:#3b5a9a"></i><i style="background:#2fa8e0"></i><i style="background:#3a3a3a;border:1px solid #777"></i><i style="background:#f0a020"></i><i style="background:#c4221f"></i><i style="background:#8fa4b4"></i>
  </div>
  <div class="footer-links abs">Home | Careers | Services | Clients | About us<br>Home © 2014 &nbsp;bluefernbs. All rights reserved.</div>
</footer>

</body>
</html>
```